Flat bootstrap design for existing site

I'm looking for a modern flat design based around an existing logo. This has to be a custom design (no external templates), and implemented into a bootstrap framework.

The logo is attached as 2 versions - choose whichever you want, that flows better with whatever design you choose.

Added screenshots of the existing site (currently using the default bootstrap layouts). Please make your designs around those pages in the screenshots (i.e. the homepage only has the postal code input and the header). The active page has 3 screenshots, because I wanted to illustrate the other states that would be visible (in the table rows).

This is a moving/junk removal website, just for some context.

Here's some example websites (flat designs) that I like, just to give you an idea of what I'm after.

https://www.plimvora.com/
https://dacklow.com/
https://trevanu.com/
https://quobrintal.com/en/

Coding

Coded - Design and coding required

Number of Pages Required

5+ page

Colors

Designer to choose colors to be used in the design.

Requirements
Must have
• It must be a modern/simple flat design, that is built around the existing logo (attached).
• It has to be implemented using bootstrap.

```html
<!DOCTYPE html>
<html lang="en">
<head>
<meta charset="utf-8">
<title>Haulvix – Book Junk Removal</title>
<link href="https://fonts.googleapis.com/css2?family=Raleway:wght@400;500;600;700;800&display=swap" rel="stylesheet">
<style>
  :root {
    --sky: #56cdf6;
    --sky-deep: #48c6f3;
    --white: #ffffff;
    --ink: #333333;
    --muted: #555555;
    --panel: #f9f9f9;
    --panel-line: #e6e6e6;
    --field-line: #dddddd;
    --action: #3f7bb3;
  }
  * { box-sizing: border-box; margin: 0; padding: 0; }
  html, body {
    width: 1200px; height: 1009px; overflow: hidden;
    background: var(--white);
    font-family: "Raleway", sans-serif;
  }
  .page { position: relative; width: 1200px; height: 1009px; }

  .site-header {
    position: absolute; left: 0; top: 0; width: 1200px; height: 75px;
    background: linear-gradient(90deg, var(--sky), var(--sky-deep));
  }
  .brand {
    position: absolute; left: 100px; top: 0; height: 75px;
    display: flex; align-items: center; gap: 8px;
    color: var(--white); font-weight: 800; font-size: 30px; letter-spacing: 1px;
    text-transform: uppercase;
  }
  .brand-dot { width: 14px; height: 14px; border-radius: 50%; background: var(--white); }
  .main-nav {
    position: absolute; top: 0; right: 100px; height: 75px;
    display: flex; list-style: none;
  }
  .main-nav li a {
    display: flex; align-items: center; height: 75px; padding: 0 22px;
    color: var(--white); text-decoration: none;
    font-size: 13px; font-weight: 500; text-transform: uppercase;
  }
  .main-nav li:last-child a { padding-right: 0; }
  .main-nav li.is-active a { background: var(--white); color: var(--sky-deep); }

  .booking-panel {
    position: absolute; left: 99px; top: 99px; width: 1003px; height: 277px;
    background: var(--panel); border: 1px solid var(--panel-line);
    text-align: center;
  }
  .booking-title {
    margin-top: 67px;
    font-size: 40px; font-weight: 500; color: var(--ink); text-transform: uppercase;
    letter-spacing: -0.3px;
  }
  .booking-form {
    position: absolute; left: 280px; top: 152px;
    display: flex; gap: 8px;
  }
  .postal-field {
    width: 335px; height: 49px; padding: 0 16px;
    border: 1px solid var(--field-line); background: var(--white);
    font-family: "Raleway", sans-serif; font-size: 12.5px; color: var(--muted);
  }
  .postal-field::placeholder { color: var(--muted); }
  .book-button {
    width: 101px; height: 49px; border: 0; background: var(--action);
    color: var(--white); font-family: "Raleway", sans-serif;
    font-size: 14.5px; font-weight: 700; letter-spacing: 2px;
  }

  .site-footer {
    position: absolute; left: 0; top: 962px; width: 1200px; height: 47px;
    background: linear-gradient(90deg, var(--sky), var(--sky-deep));
    display: flex; align-items: center; justify-content: center;
    color: var(--white); font-size: 12.5px;
  }
</style>
</head>
<body>
<div class="page">
  <header class="site-header">
    <div class="brand"><span class="brand-dot"></span>Haulvix</div>
    <ul class="main-nav">
      <li><a href="#">Book</a></li>
      <li><a href="#">How it works</a></li>
      <li class="is-active"><a href="#">Become a driver</a></li>
      <li><a href="#">Sign in</a></li>
    </ul>
  </header>

  <section class="booking-panel">
    <h1 class="booking-title">Need junk removed ? Book now.</h1>
    <form class="booking-form">
      <input class="postal-field" type="text" placeholder="Postal Code">
      <button class="book-button" type="button">BOOK</button>
    </form>
  </section>

  <footer class="site-footer">© copyright 2017 Haulvix.All Rights Reserved</footer>
</div>
</body>
</html>
```